Anzeigengestaltung für Unternehmensberatung für Pflegedienste
Zielgruppe
Wir sind eine Unternehmensberatung für Pflegedienste. Es soll eine Werbeanzeige erstellt werden, mit welcher schlecht laufende Pflegedienste, die gerade in einer Krise stecken angesprochen werden,
Der slogan soll einfach klingen : Pflege neu gedaxht: wirtschaftlich, nachhaltig, zukunftssicher
Anzeige in 3 Formaten
1. Format 55.3 mm x 118 mm
2. Format 1/ halbe Seite Quer 176 x 118 mm un
3. Format d 1 x A4 _Seite
Der Name der Firma Tolvek GmbH info at tolvek-beispiel.de Tel 0555 91827364 aus Rostock Berlin und bundesweit tätig
Aufgabenstellung
Kreativ und elegant

```html
<!DOCTYPE html>
<html lang="de">
<head>
<meta charset="utf-8">
<title>Tolvek GmbH – Pflege neu gedacht</title>
<link rel="stylesheet" href="https://fonts.googleapis.com/css2?family=Newsreader:opsz,wght@6..72,400&family=Montserrat:wght@400&display=swap">
<style>
  :root {
    --paper: #f2eee6;
    --navy: #1f2a44;
    --navy-soft: #3a4663;
    --gold: #d4a956;
    --ink: #1c2438;
  }
  * { margin: 0; padding: 0; box-sizing: border-box; }
  html, body {
    width: 1200px;
    height: 900px;
    overflow: hidden;
    background: var(--paper);
  }
  .ad {
    position: relative;
    width: 1200px;
    height: 900px;
    background: var(--paper);
    overflow: hidden;
  }
  .hands-illustration {
    position: absolute;
    left: 0;
    top: 0;
    width: 640px;
    height: 900px;
    background:
      radial-gradient(circle at 370px 320px, rgba(212,169,86,0.5) 0, rgba(212,169,86,0) 80px),
      radial-gradient(ellipse 220px 150px at 340px 130px, rgba(31,42,68,0.8) 0, rgba(31,42,68,0) 100%),
      radial-gradient(ellipse 250px 130px at 240px 560px, rgba(31,42,68,0.8) 0, rgba(31,42,68,0) 100%),
      radial-gradient(ellipse 190px 130px at 290px 760px, rgba(58,70,99,0.75) 0, rgba(58,70,99,0) 100%),
      radial-gradient(circle at 330px 800px, rgba(212,169,86,0.3) 0, rgba(212,169,86,0) 100px);
  }
  .brand {
    position: absolute;
    left: 762px;
    top: 72px;
    font-family: "Newsreader", Georgia, serif;
    font-weight: 400;
    font-size: 90px;
    letter-spacing: 1px;
    line-height: 1;
    color: var(--navy);
  }
  .slogan {
    position: absolute;
    left: 596px;
    top: 338px;
    font-family: "Newsreader", Georgia, serif;
    font-weight: 400;
    font-size: 59px;
    line-height: 64px;
    color: var(--ink);
  }
  .contact {
    position: absolute;
    left: 592px;
    top: 786px;
    font-family: "Montserrat", Arial, sans-serif;
    font-size: 14px;
    color: var(--ink);
    white-space: nowrap;
  }
  .contact .sep { margin: 0 5px; }
</style>
</head>
<body>
  <main class="ad">
    <div class="hands-illustration" role="img" aria-label="Illustration: zwei Hände reichen sich entgegen, dazwischen schwebende Säulen und Kreise in Marineblau und Gold"></div>

    <div class="brand">TOLVEK</div>

    <p class="slogan">“Pflege neu gedacht:<br>wirtschaflich,<br>nachhaltig,<br>zukunftssicher”</p>

    <p class="contact">Info@tolvek-beispiel.de<span class="sep">|</span>Tel 0555 91827364<span class="sep">|</span>Rostock, Berlin &amp; Nationwide</p>
  </main>
</body>
</html>
```